Website Redesign Project

Brightwater Delivery Partners provides project management and project controls consultancy services to companies in many industry sectors, within Australia and overseas. My company has been developing a business brand through forging strong business relationships within industry. We provide innovative tools, concepts and solutions to management teams to assist them in better plan and managing there project portfolios.
SECTORS OF INDUSTRY WE SERVICE
★Oil & Gas
★Minerals & Metals
★Petrochemical
★Manufacturing
★Building & Construction
★Telecommunications
★Rail
★Civil
OLD WEBSITE
My old website www.brightwaterdeliverypartners-demo.com.au needs a complete overhaul in terms of how the web pages look and feel. I am trying to get away from the grey, washed out look as it is uninviting and dull. My clients commented that my webpage does not reflect who I am as a company or my core values. Think total redesign
DESIGN
I would like a webpage design that is modern and has a corporate image. It must be elegant, classy, and have an overall glossy appearance. I want something exciting that creates some excellent feedback from clients. It needs to have a savvy appearance and an attitude of a market leader. A generic website template cannot be used as I provide a unique service to clients. I do not need a website design that looks like my compeditors, I want something that stands out in the crowd and effectivly markets my bussinesses brand. I want my website to represent quality, so only high resolution images that are clear, sharp and in focus can be used. With this design, throw your standard webpage design concepts out the window, as I want something fresh, innovative, exciting and inviting. The overall design should appear uncluttered as all content needs to be there for a reason, so think functional.
It must be professional and of the highest calibre as my clients expect nothing less. I provide clients with innovative tools, concepts and solutions, so the design needs to be edgy and creative to align with my company’s core business services. The new design must promote the company’s brand and us as a market leader. It must communicate that we service many industry sectors and reflect our company’s creativity, vision, energy and drive.
WEBPAGE WRITTEN CONTENT
I am happy with the written content on each page within my old website. You may arrange the text how you see fit within the new design. On the main page of my old website the text is under scored, I am not a big fan of this. I currently do not like the format the text is in, I am looking for a formatt that is easy to read, looks flattering and pleasing to the eye.
MAIN PAGE DESIGN
The main page design needs to focus on my company as a brand, it must promote that I service many industry sectors. My old webpage had me pigeon holed as only providing services to oil and gas. This is incorrect as I service oil & gas, metals and minerals, Petrochemical, Manufacturing, Building & Construction, Telecommunications, Rail and civil.
WEBPAGE COLUR PREFERENCE
Prefer a white background with plenty of colour
TESTIMONIAL TAB
The testimonial tab on the task bar can be removed as it is no longer required.
FINISHED PRODUCT
The finished product will be uploaded by you to a nominated web hosting account. I will need a copy of all files associated with the design. A copy of the finished product will also be provided in formats that can me imported to Xara Pro Designer as I will update my website in 6 months or so using this tool.
Updates
I have updated the design brief after recieving feedback from several designers
Thanks
Reason: Some designers have asked for more time
Hi All
I have just launched another project called "brightwater delivery partners business card redesign project", you are all welcome to join this project.
Thanks
Target Market(s)
★Oil and Gas
★Mining and Resources
★Building and infrastructure
★Petrochemical
★Civil and roads
★Rail
Industry/Entity Type
Industry
Requirements
Must have
- ★Draw you in
★Hold your attention
★Identify company brand
★Highlight skills experience and expertise
★Be a unique design not generic
Should not have
- ★The webpage design should not be old fashioned
★ The design should not be based off a generic design template
★The webpage should not be cluttered; everything needs to be there for a reason.

```html
<!DOCTYPE html>
<html lang="en">
<head>
<meta charset="utf-8">
<title>Brightwater Delivery Partners</title>
<link href="https://fonts.googleapis.com/css2?family=Source+Sans+3:wght@400;600;700&display=swap" rel="stylesheet">
<style>
:root{
  --red:#e3202a;
  --red-dark:#b8141c;
  --ink:#1d1d1d;
  --text:#4a4a4a;
  --muted:#8a8a8a;
  --panel:#fbfafa;
  --card:#e8e7e6;
  --bar:#1f1f1f;
  --footer:#262626;
  --white:#ffffff;
}
*{box-sizing:border-box;margin:0;padding:0}
html,body{width:1003px;height:1200px;overflow:hidden}
body{position:relative;background:var(--white);font-family:"Source Sans 3",Arial,sans-serif;color:var(--text)}
.topbar{position:absolute;left:0;top:0;width:1003px;height:47px;background:linear-gradient(#3a3a3a,#0f0f0f 60%,#1c1c1c);color:#eee;font-size:14px}
.topbar .contact{position:absolute;top:16px;display:flex;align-items:center;gap:9px}
.topbar .contact svg{fill:#9a9a9a}
.topbar .phone{left:82px}
.topbar .email{left:256px}
.social{position:absolute;display:flex;gap:14px}
.social span{width:10px;height:10px;border-radius:50%;background:#9a9a9a;display:block}
.topbar .social{right:80px;top:19px}
.brand{position:absolute;left:86px;top:62px;display:flex;align-items:center;gap:12px}
.brand .mark{width:58px;height:58px;border-radius:50%;background:var(--red)}
.brand .name{font-size:25px;font-weight:700;color:var(--ink);line-height:1}
.brand .tagline{font-size:10px;color:var(--ink);margin-top:6px}
.search{position:absolute;left:733px;top:91px;width:189px;height:29px;border:1px solid #cfcfcf;border-radius:4px;font-size:12px;font-style:italic;color:#999;padding:6px 9px}
.search svg{position:absolute;right:9px;top:7px}
.panel{position:absolute;left:70px;top:150px;width:865px;height:958px;background:var(--panel)}
.nav{position:absolute;left:84px;top:163px;width:839px;height:40px;border-radius:5px;background:linear-gradient(#f0343c,var(--red) 50%,#cf1820);display:flex;box-shadow:0 1px 2px rgba(0,0,0,.3)}
.nav a{color:var(--white);text-decoration:none;font-size:14px;line-height:40px;padding:0 14px;border-right:1px solid rgba(0,0,0,.18);flex:auto;text-align:center}
.nav a:last-child{border-right:0}
.hero{position:absolute;left:85px;top:212px;width:839px;height:338px;background:radial-gradient(ellipse at 55% 50%,#c98a3c 0%,#7a4f22 25%,#2a1c10 55%,#111 80%)}
.hero-shadow{position:absolute;left:140px;top:548px;width:730px;height:30px;background:radial-gradient(ellipse at 50% 0%,rgba(0,0,0,.22),transparent 70%)}
.hero-arrows{position:absolute;left:104px;top:516px;width:34px;height:22px;background:#111;display:flex;justify-content:space-around;align-items:center}
h2{font-weight:400;color:var(--ink);font-size:19px;position:absolute}
.services-title{left:84px;top:587px}
.services-arrows{position:absolute;left:890px;top:588px;display:flex;gap:10px}
.card{position:absolute;top:623px;width:191px;height:207px;border-radius:7px;background:var(--card);padding:10px 7px}
.card .photo{width:177px;height:126px}
.card h3{font-size:12px;font-weight:700;color:#333;margin-top:9px;letter-spacing:.2px}
.card p{font-size:12px;line-height:18px;color:#666;margin-top:3px}
.card.active{background:var(--red)}
.card.active h3,.card.active p{color:var(--white)}
.welcome-title{left:83px;top:892px}
.lead{position:absolute;left:84px;top:927px;font-size:13px;color:#333;text-transform:uppercase}
.body-copy{position:absolute;left:84px;top:954px;width:550px;font-size:11.5px;line-height:19px;color:#555}
.body-copy p+p{margin-top:3px}
.testi-title{left:690px;top:891px}
.testi-arrows{position:absolute;left:884px;top:891px;display:flex;gap:3px}
.testi-arrows span{width:18px;height:18px;border-radius:50%;background:#b5b5b5;display:flex;align-items:center;justify-content:center}
.quote{position:absolute;left:689px;top:932px;width:236px;font-size:11.5px;line-height:19px;color:#555}
.quote p+p{margin-top:2px}
.quote cite{display:block;text-align:right;color:var(--red);font-style:normal;font-size:13px}
.footer{position:absolute;left:0;top:1108px;width:1003px;height:92px;background:var(--footer);color:#ddd}
.copy{position:absolute;left:91px;top:36px;font-size:12px}
.newsletter{position:absolute;left:527px;top:33px;font-size:14px;color:var(--white)}
.news-field{position:absolute;left:604px;top:28px;width:169px;height:29px;background:var(--white);border-radius:3px}
.news-field svg{position:absolute;right:5px;top:8px}
.footer .social{left:806px;top:40px;gap:20px}
.footer .social span{background:#e5e5e5}
</style>
</head>
<body>
<header class="topbar">
  <div class="contact phone"><svg width="14" height="12" viewBox="0 0 14 12"><path d="M1 3c0-2 12-2 12 0v2h-3V3.5H4V5H1zM3 6h8l2 5H1z"/></svg>+61 0400 555 012</div>
  <div class="contact email"><svg width="15" height="10" viewBox="0 0 15 10"><path d="M0 0h15v10H0z M1 1l6.5 5L14 1z" fill-rule="evenodd"/></svg>hello@brightwaterdeliverypartners-demo.com.au</div>
  <div class="social"><span></span><span></span><span></span><span></span></div>
</header>

<div class="brand">
  <div class="mark"></div>
  <div>
    <div class="name">Brightwater Delivery Partners</div>
    <div class="tagline">Providing Effective Project Controls and Management Solutions</div>
  </div>
</div>
<div class="search">Search..<svg width="12" height="12" viewBox="0 0 12 12"><circle cx="5" cy="5" r="4" fill="none" stroke="#888" stroke-width="1.6"/><path d="M8 8l3 3" stroke="#888" stroke-width="1.8"/></svg></div>

<div class="panel"></div>
<nav class="nav">
  <a>Home</a><a>About Us</a><a>Expertise</a><a>Knowledge</a><a>Experience</a><a>Projects</a><a>Focus</a><a>Contact</a><a>Testimonials</a><a>Recruitment</a>
</nav>

<div class="hero" role="img" aria-label="Photograph of illuminated industrial pipework in a plant corridor"></div>
<div class="hero-shadow"></div>
<div class="hero-arrows"><svg width="8" height="12"><path d="M6 1L2 6l4 5" stroke="#fff" fill="none" stroke-width="1.5"/></svg><svg width="8" height="12"><path d="M2 1l4 5-4 5" stroke="#fff" fill="none" stroke-width="1.5"/></svg></div>

<h2 class="services-title">Our Services</h2>
<div class="services-arrows"><svg width="10" height="16"><path d="M8 1L2 8l6 7" stroke="#ccc" fill="none" stroke-width="2.5"/></svg><svg width="10" height="16"><path d="M2 1l6 7-6 7" stroke="#111" fill="none" stroke-width="2.5"/></svg></div>

<article class="card active" style="left:84px">
  <div class="photo" role="img" aria-label="Refinery towers silhouetted against an orange sunset" style="background:linear-gradient(#f6b21a,#e07a10 60%,#3a2005)"></div>
  <h3>OIL &amp; GAS</h3>
  <p>Sedianommy nibh euismode loren tincidunt laores.</p>
</article>
<article class="card" style="left:301px">
  <div class="photo" role="img" aria-label="Molten metal glowing in a dark foundry" style="background:radial-gradient(circle at 42% 45%,#f2a04a,#7a3a18 30%,#1a0e08 70%)"></div>
  <h3>MINERALS &amp; METALS</h3>
  <p>Sedianommy nibh euismode loren tincidunt laores.</p>
</article>
<article class="card" style="left:517px">
  <div class="photo" role="img" aria-label="Petrochemical plant lit up at dusk by the water" style="background:linear-gradient(#2f5fa8,#4a78b8 50%,#c9a064 75%,#22324a)"></div>
  <h3>PETROCHEMICAL</h3>
  <p>Sedianommy nibh euismode loren tincidunt laores.</p>
</article>
<article class="card" style="left:732px">
  <div class="photo" role="img" aria-label="Worker assembling an engine on a factory line" style="background:linear-gradient(135deg,#4d8a52,#8a9a8a 50%,#5a5f64)"></div>
  <h3>MANUFACTURING</h3>
  <p>Sedianommy nibh euismode loren tincidunt laores.</p>
</article>

<h2 class="welcome-title">Welcome to Brightwater Delivery Partners</h2>
<div class="lead">Tempor incididunt ut labore et dolore magna aliqua. Ut enim ad minim veniam</div>
<div class="body-copy">
  <p>Incididunt ut labore et dolore magna aliqua. Ut enim ad minim veniam, quis nostrud exercitation ullamco laboris nisi ut aliquip ex ea commodo consequat. Duis tefd aute irure dolor in reprehenderit in voluptate velit esse cillum.</p>
  <p>Dolore magna aliqua. Ut enim ad minim veniam, quis nostrud exercitation ullamco laboris nisi ut aliquip ex ea commodo consequat. Duis aute irure dolor in reprehenderit in voluptate velit esse cillum dolore eu fugiat nul a pariatur. Excepteur sint occaecat cupidatat non proident.</p>
</div>

<h2 class="testi-title">Testimonials</h2>
<div class="testi-arrows"><span><svg width="6" height="9"><path d="M5 1L1 4.5 5 8" stroke="#fff" fill="none" stroke-width="1.6"/></svg></span><span><svg width="6" height="9"><path d="M1 1l4 3.5L1 8" stroke="#fff" fill="none" stroke-width="1.6"/></svg></span></div>
<blockquote class="quote">
  <p>Fusce feugiat malesuada odio. Morbi nunc odio gravida at, cursusi nec, luctus a, lorem. Maecenas tristique orci acd sem. Duis ultricies pharetra magna. Donec accumsan malesuada orci.</p>
  <p>Lorem ipsum dolor sit amet, consectetuer adipiscing elit.</p>
  <cite>- Sam Marlow</cite>
</blockquote>

<footer class="footer">
  <div class="copy">Copyrights 2013. All Rights Reserved.</div>
  <div class="newsletter">Newsletter</div>
  <div class="news-field"><svg width="14" height="14"><path d="M2 1l5 6-5 6M7 1l5 6-5 6" stroke="#777" fill="none" stroke-width="1.4"/></svg></div>
  <div class="social"><span></span><span></span><span></span><span></span></div>
</footer>
</body>
</html>
```